Manuka Honey company needs a Upmarket, Luxury Website!

New Zealand, Taranaki based Manuka Honey company Rimu Vale Honey is looking for a new website, we are looking for an upmarket, luxury, serious website design. We export the highest quality quality Manuka Honey, straight from the Taranaki region.

Main export markets are Asia & Europe, also New Zealand & Australia.

Looking to have a beautiful, upmarket, serious, luxurious & graphical experience with mobile optimization in mind. Like the use of product staging/mockups

You can use copy from other websites to build the site and we will change the copy after the design is finished.

***Please include 'Honey Product' mockups in website.

*Will add illustrator files in coming days***

Feel free to make website functional in Shopify, Wordpress or WIX

Target Market(s)

Asia, Europe (main markets) New Zealand, Australia (Submarkets)

Coding

Coded - Design and coding required

Number of Pages Required

4 page

Requirements
Must have
• Home, Shop, About Us, Contact Us

Homepage to include:

Our Products
Company Video (video under construction)
What is MGO/KPS
Newsletter Opt-in

***(Not in Order)***

Please include 'Honey Product' mockups in website.
*Will add illustrator files in coming days
Nice to have
• FAQ & Partnership Inquiries (hyperlink in footer)

```html
<!DOCTYPE html>
<html lang="en">
<head>
<meta charset="utf-8">
<title>Rimu Vale Honey — Manuka Honey</title>
<link href="https://fonts.googleapis.com/css2?family=Montserrat:wght@300;400;500;600;700;800&display=swap" rel="stylesheet">
<style>
  :root{
    --ink:#1b1b1b;
    --text:#4a4a4a;
    --gold:#e6b32b;
    --gold-soft:#d9a93a;
    --orange-a:#f7a21b;
    --orange-b:#ec4f1c;
    --sky:#f3fafd;
    --card:#ffffff;
    --grey-dot:#c9c9c9;
  }
  *{box-sizing:border-box;margin:0;padding:0}
  html,body{width:1200px;height:2971px;overflow:hidden}
  body{font-family:"Montserrat",sans-serif;color:var(--ink);background:#fff}
  .page{position:relative;width:1200px;height:2971px;overflow:hidden;background:#fff}
  .abs{position:absolute}
  .btn{position:absolute;display:flex;align-items:center;justify-content:center;border-radius:24px;
    background:linear-gradient(90deg,var(--orange-a),var(--orange-b));color:#fff;font-weight:700;
    letter-spacing:.4px;text-transform:uppercase;text-decoration:none}

  /* header */
  .brand{left:127px;top:28px;font-size:26px;font-weight:400;letter-spacing:4px;color:#333}
  .nav a{position:absolute;top:34px;font-size:12.5px;font-weight:500;color:#222;text-decoration:none}
  .nav a.active{font-weight:700}
  .nav .active-bar{position:absolute;left:478px;top:0;width:40px;height:2px;background:var(--gold)}
  .cart-badge{left:1089px;top:23px;width:18px;height:18px;border-radius:50%;background:var(--gold);
    color:#fff;font-size:10px;font-weight:600;display:flex;align-items:center;justify-content:center}

  /* hero */
  .hero-bg{left:0;top:0;width:1200px;height:790px;
    background:linear-gradient(180deg,#ffffff 0%,#e9f2f8 14%,#d3e4ef 35%,#e0e8ed 60%,#f2f5f7 82%,#ffffff 100%)}
  .hero-stage{left:546px;top:120px;width:580px;height:580px;border-radius:50%;
    background:radial-gradient(circle at 55% 55%,#b5642f 0%,#8a3f1c 16%,#50603f 30%,#6f9cc6 48%,#bcd6ea 68%,#f1f6fa 88%,#ffffff 100%)}
  .hero-mark{left:297px;top:255px;width:18px;height:18px;border-radius:50%;border:2px solid #39506b}
  .hero-eyebrow{left:0;width:604px;top:306px;text-align:center;font-size:21px;font-weight:400;letter-spacing:3px;color:#222}
  .hero-eyebrow::before,.hero-eyebrow::after{content:"";display:inline-block;width:36px;height:1px;background:#888;vertical-align:middle;margin:0 14px}
  .hero-title{left:0;width:608px;top:336px;text-align:center;font-size:46px;font-weight:700;letter-spacing:4px;color:#111}
  .hero-sub{left:0;width:608px;top:399px;text-align:center;font-size:15px;line-height:26px;color:#444}
  .hero-dots span{position:absolute;left:1161px;width:12px;height:12px;border-radius:50%;background:var(--grey-dot)}

  /* company video */
  .video-frame{left:109px;top:794px;width:507px;height:348px;border-radius:0 40px 0 40px;
    background:linear-gradient(135deg,#e6e4e1 0%,#dcd8d2 38%,#c99850 58%,#b9c6a6 78%,#e9e6e2 100%)}
  .video-play{left:346px;top:936px}
  .eyebrow{font-size:17px;font-weight:400;letter-spacing:5px;color:var(--gold)}
  .section-title{font-size:33px;font-weight:700;letter-spacing:3px;color:#111}
  .video-copy{left:674px;top:894px;width:440px;font-size:11.2px;line-height:20.6px;color:var(--text)}
  .video-copy p+p{margin-top:20px}

  /* products */
  .sky-band{left:-200px;top:1190px;width:1600px;height:1560px;background:var(--sky);border-radius:50% 50% 0 0 / 120px 120px 0 0}
  .product-card{position:absolute;top:1467px;width:313px;height:369px;background:var(--card);box-shadow:0 2px 10px rgba(0,0,0,.05)}
  .product-jar{position:absolute;left:101px;top:58px;width:128px;height:153px;border-radius:16px 16px 22px 22px;
    box-shadow:0 10px 14px -8px rgba(0,0,0,.35)}
  .jar-blue{background:linear-gradient(180deg,#2a2a2a 0%,#23365c 30%,#1d4a8c 60%,#172e5a 100%)}
  .jar-green{background:linear-gradient(180deg,#2a2a2a 0%,#1f4b30 30%,#2a7044 60%,#1a3d27 100%)}
  .jar-black{background:linear-gradient(180deg,#2a2a2a 0%,#4a4843 32%,#e9e4d7 55%,#4a4843 78%,#1d1d1d 100%)}
  .product-name{position:absolute;left:0;width:100%;top:241px;text-align:center;font-size:17px;font-weight:500;letter-spacing:.5px;color:#333}
  .product-price{position:absolute;left:0;width:100%;top:268px;text-align:center;font-size:16px;font-weight:600;color:#333}
  .product-card .btn{left:83px;top:309px;width:146px;height:39px;font-size:12px}
  .slider-arrow{width:32px;height:32px;border-radius:50%;background:#8a8a8a;display:flex;align-items:center;justify-content:center}
  .btn-outline{left:476px;top:1887px;width:237px;height:48px;border:2px solid #2a2a2a;border-radius:26px;
    display:flex;align-items:center;justify-content:center;font-size:13.5px;font-weight:700;color:#222;letter-spacing:.3px;text-decoration:none}

  /* mgo / kps */
  .kps-ring{left:141px;top:2112px;width:426px;height:426px;border-radius:50%;border:2px solid #dfe3e6}
  .kps-sun{left:166px;top:2139px;width:376px;height:376px;border-radius:50%;
    background:radial-gradient(circle at 45% 40%,#f6c43a 0%,#eda91c 55%,#e29a14 100%)}
  .kps-jars{left:239px;top:2419px;width:262px;height:190px;border-radius:24px;
    background:linear-gradient(90deg,#1d4a2f 0%,#2a6a42 30%,#7a3a1a 62%,#a24a1e 100%);
    box-shadow:0 14px 20px -10px rgba(0,0,0,.35)}
  .kps-dot{width:12px;height:12px;border-radius:50%;background:#111}
  .kps-icon{width:76px;height:76px;border-radius:50%;border:2px solid #e8ebed;background:#fff;display:flex;align-items:center;justify-content:center}
  .kps-item .k1{font-size:15px;letter-spacing:1.8px;font-weight:400;color:#222}
  .kps-item .k2{font-size:15px;letter-spacing:2px;font-weight:700;color:#111}
  .kps-item .k3{font-size:11px;color:#555;margin-top:5px;padding-left:4px}

  /* footer */
  .footer{left:0;top:2706px;width:1200px;height:265px;background:linear-gradient(180deg,#121212 0%,#1b1b1b 40%,#0d0d0d 100%)}
  .foot-rule{height:1px;background:#6d5a2a}
  .foot-nav a{position:absolute;top:2813px;font-size:12.5px;color:#cfcfcf;text-decoration:none}
  .foot-nav a.hl{color:var(--gold);font-weight:700}
  .foot-seal{left:541px;top:2766px;width:112px;height:112px;border-radius:50%;border:2px solid var(--gold-soft);
    display:flex;align-items:center;justify-content:center;text-align:center;color:var(--gold-soft);font-size:11px;font-weight:600;letter-spacing:1.5px;line-height:16px;background:#111}
  .foot-copy{left:160px;top:2881px;font-size:11px;color:#c9a64a}
  .foot-legal{left:160px;top:2906px;font-size:9px;color:#c9a64a}
  .newsletter{left:420px;top:2897px;width:360px;display:flex;align-items:center;gap:0}
  .newsletter-label{position:absolute;left:420px;top:2888px;width:360px;text-align:center;font-size:10px;letter-spacing:3px;color:var(--gold)}
  .newsletter-field{flex:1;height:34px;border:1px solid #6d5a2a;border-right:none;border-radius:17px 0 0 17px;background:#161616;
    color:#9a9a9a;font-size:11px;display:flex;align-items:center;padding-left:16px}
  .newsletter-btn{width:110px;height:34px;border-radius:0 17px 17px 0;background:linear-gradient(90deg,var(--orange-a),var(--orange-b));
    color:#fff;font-size:11px;font-weight:700;display:flex;align-items:center;justify-content:center;letter-spacing:.4px}
  .social{width:32px;height:32px;border-radius:50%;border:2px solid var(--gold-soft);display:flex;align-items:center;justify-content:center}
  .social i{display:block;width:12px;height:12px;border-radius:50%;background:#e6e6e6}
</style>
</head>
<body>
<div class="page">

  <div class="abs hero-bg" role="img" aria-label="Misty snow-capped mountain range under clouds"></div>
  <div class="abs hero-stage" role="img" aria-label="Mountain peaks in a round cloud frame with two jars of premium manuka honey"></div>

  <header>
    <div class="abs brand">RIMU VALE HONEY</div>
    <nav class="nav">
      <span class="active-bar"></span>
      <a class="active" style="left:480px" href="#">HOME</a>
      <a style="left:591px" href="#">SHOP</a>
      <a style="left:701px" href="#">ABOUT US</a>
      <a style="left:840px" href="#">CONTACT US</a>
    </nav>
    <svg class="abs" style="left:970px;top:33px" width="22" height="22" viewBox="0 0 22 22" fill="none" stroke="#333" stroke-width="1.6"><circle cx="9" cy="9" r="7"/><path d="M14 14l6 6"/></svg>
    <svg class="abs" style="left:1015px;top:30px" width="22" height="22" viewBox="0 0 22 22" fill="none" stroke="#333" stroke-width="1.6"><circle cx="11" cy="7" r="5"/><path d="M2 21c0-5 4-8 9-8s9 3 9 8z"/></svg>
    <svg class="abs" style="left:1060px;top:31px" width="24" height="22" viewBox="0 0 24 22" fill="none" stroke="#333" stroke-width="1.6"><path d="M1 2h4l3 12h12l2-9H6"/><circle cx="9" cy="19" r="1.6"/><circle cx="19" cy="19" r="1.6"/></svg>
    <div class="abs cart-badge">0</div>
  </header>

  <section class="hero">
    <span class="abs hero-mark"></span>
    <div class="abs hero-eyebrow">RIMU VALE HONEY CO.</div>
    <h1 class="abs hero-title">MANUKA HONEY</h1>
    <p class="abs hero-sub">Curabitur vel dolor ultrices ipsum dictum<br>tristique Praesent vitae lacus velit</p>
    <a class="btn" style="left:213px;top:470px;width:169px;height:45px;font-size:15px" href="#">SHOP NOW</a>
    <div class="hero-dots">
      <span style="top:341px;background:var(--gold)"></span>
      <span style="top:366px"></span>
      <span style="top:392px"></span>
    </div>
  </section>

  <section class="video">
    <div class="abs video-frame" role="img" aria-label="Bowl of honey with wooden dipper beside flowering manuka branches"></div>
    <svg class="abs video-play" width="36" height="50" viewBox="0 0 36 50"><path d="M0 0L36 25L0 50Z" fill="#fff"/></svg>
    <div class="abs eyebrow" style="left:669px;top:812px">WHO WE ARE</div>
    <h2 class="abs section-title" style="left:668px;top:838px">OUR COMPANY VIDEO</h2>
    <div class="abs video-copy">
      <p>Lorem Ipsum is simply dummy text of the printing and typesetting indus-try. Lorem Ipsum has been the industry's standard dummy text ever since the 1500s, when an unknown printer took a galley of type and scrambled it to make a type specimen book. It has survived not only five centuries</p>
      <p>was popularised in the 1960s with the release of Markwell sheets contain-ing Lorem Ipsum passages, and more recently with desktop publishing software like Quillset Layout including versions of</p>
    </div>
    <a class="btn" style="left:672px;top:1086px;width:166px;height:44px;font-size:14px" href="#">LEARN MORE</a>
  </section>

  <div class="abs sky-band"></div>
  <section class="products">
    <div class="abs eyebrow" style="left:0;width:1203px;top:1349px;text-align:center">FEATURED</div>
    <h2 class="abs section-title" style="left:0;width:1196px;top:1376px;text-align:center">OUR PRODUCTS</h2>

    <div class="abs slider-arrow" style="left:42px;top:1636px"><svg width="12" height="14" viewBox="0 0 12 14"><path d="M8 2L3 7l5 5" stroke="#fff" stroke-width="2.4" fill="none"/></svg></div>
    <div class="abs slider-arrow" style="left:1113px;top:1636px"><svg width="12" height="14" viewBox="0 0 12 14"><path d="M4 2l5 5-5 5" stroke="#fff" stroke-width="2.4" fill="none"/></svg></div>

    <article class="product-card" style="left:96px">
      <div class="product-jar jar-blue" role="img" aria-label="Product mockup: jar of manuka honey with blue label"></div>
      <div class="product-name">MONUKA HOENY</div>
      <div class="product-price">$10.99 USD</div>
      <a class="btn" href="#">SHOP NOW</a>
    </article>
    <article class="product-card" style="left:436px">
      <div class="product-jar jar-green" role="img" aria-label="Product mockup: jar of manuka honey with green label"></div>
      <div class="product-name">MONUKA HOENY</div>
      <div class="product-price">$10.99 USD</div>
      <a class="btn" href="#">SHOP NOW</a>
    </article>
    <article class="product-card" style="left:778px">
      <div class="product-jar jar-black" role="img" aria-label="Product mockup: jar of manuka honey with black and white label"></div>
      <div class="product-name">MONUKA HOENY</div>
      <div class="product-price">$10.99 USD</div>
      <a class="btn" style="top:305px" href="#">SHOP NOW</a>
    </article>

    <a class="abs btn-outline" href="#">VIEW ALL PRODUCTS</a>
  </section>

  <section class="kps">
    <h2 class="abs section-title" style="left:0;width:1220px;top:2004px;text-align:center;font-size:27px">WHAT IS MGO/KPS</h2>
    <div class="abs kps-ring"></div>
    <div class="abs kps-sun" role="img" aria-label="Golden honey circle backdrop"></div>
    <div class="abs kps-jars" role="img" aria-label="Product mockup: two jars of manuka honey, green and amber labels"></div>
    <span class="abs kps-dot" style="left:490px;top:2161px"></span>
    <span class="abs kps-dot" style="left:547px;top:2248px"></span>
    <span class="abs kps-dot" style="left:559px;top:2341px"></span>
    <span class="abs kps-dot" style="left:529px;top:2435px"></span>

    <div class="abs kps-icon" style="left:521px;top:2097px"><svg width="40" height="34" viewBox="0 0 40 34" fill="none" stroke="#e6b32b" stroke-width="2"><path d="M8 3h6l3 5-3 5H8L5 8z"/><path d="M20 3h6l3 5-3 5h-6l-3-5z"/><path d="M14 13h6l3 5-3 5h-6l-3-5z"/><path d="M26 13h6l3 5-3 5h-6l-3-5z"/><path d="M8 23h6l3 5-3 5H8l-3-5z"/></svg></div>
    <div class="abs kps-item" style="left:612px;top:2097px"><div class="k1">CERTIFIED KPS</div><div class="k2">SUPER PREIMUM</div><div class="k3">Lorem ipsum dolor sit amet, consectetur adipiscing elit, sed do ei</div></div>

    <div class="abs kps-icon" style="left:594px;top:2208px"><svg width="30" height="34" viewBox="0 0 30 34" fill="none" stroke="#e6b32b" stroke-width="2"><rect x="7" y="2" width="16" height="6" rx="2"/><path d="M5 8h20v20a4 4 0 0 1-4 4H9a4 4 0 0 1-4-4z"/><circle cx="15" cy="19" r="5"/></svg></div>
    <div class="abs kps-item" style="left:681px;top:2207px"><div class="k1">CERTIFIED KPS</div><div class="k2">ULTRA PREIMUM</div><div class="k3">Lorem ipsum dolor sit amet, consectetur adipiscing elit, se</div></div>

    <div class="abs kps-icon" style="left:605px;top:2320px"><svg width="34" height="30" viewBox="0 0 34 30" fill="none" stroke="#e6b32b" stroke-width="2"><ellipse cx="17" cy="18" rx="7" ry="9"/><path d="M10 16h14M10 21h14"/><ellipse cx="9" cy="9" rx="7" ry="4"/><ellipse cx="25" cy="9" rx="7" ry="4"/></svg></div>
    <div class="abs kps-item" style="left:689px;top:2324px"><div class="k1">CERTIFIED KPS</div><div class="k2">SUPER PREIMUM</div><div class="k3">Lorem ipsum dolor sit amet, consectetur adipiscing elit,</div></div>

    <div class="abs kps-icon" style="left:563px;top:2436px"><svg width="30" height="38" viewBox="0 0 30 38" fill="none" stroke="#e6b32b" stroke-width="2"><circle cx="15" cy="14" r="12"/><path d="M9 14l4 4 8-8"/><path d="M8 24l-3 12 6-3 4 4M22 24l3 12-6-3-4 4"/></svg></div>
    <div class="abs kps-item" style="left:655px;top:2451px"><div class="k1">CERTIFIED KPS</div><div class="k2">SUPER PREIMUM</div><div class="k3">Lorem ipsum dolor sit amet, consectetur adipiscing elit,</div></div>
  </section>

  <footer>
    <div class="abs footer" role="img" aria-label="Dark mountain silhouette at night"></div>
    <div class="abs foot-rule" style="left:145px;top:2794px;width:377px"></div>
    <div class="abs foot-rule" style="left:145px;top:2850px;width:377px"></div>
    <div class="abs foot-rule" style="left:673px;top:2794px;width:378px"></div>
    <div class="abs foot-rule" style="left:673px;top:2850px;width:378px"></div>
    <nav class="foot-nav">
      <a class="hl" style="left:164px" href="#">HOME</a>
      <a style="left:275px" href="#">SHOP</a>
      <a style="left:385px" href="#">ABOUT US</a>
      <a class="hl" style="left:701px" href="#">BLOGS</a>
      <a style="left:816px" href="#">RESOURCES</a>
      <a class="hl" style="left:963px" href="#">CONTACT US</a>
    </nav>
    <div class="abs foot-seal">RIMU VALE<br>HONEY CO.</div>

    <div class="newsletter-label">NEWSLETTER</div>
    <form class="abs newsletter" style="top:2907px">
      <div class="newsletter-field">Your email address</div>
      <div class="newsletter-btn">SUBSCRIBE</div>
    </form>

    <div class="abs foot-copy">Copyright © 2021 RIMU VALE HONEY CO.</div>
    <div class="abs foot-legal">Terms of Use &nbsp;|&nbsp; Privacy Policy</div>
    <a class="abs social" style="left:925px;top:2881px" aria-label="Social profile"><i></i></a>
    <a class="abs social" style="left:965px;top:2881px" aria-label="Social profile"><i></i></a>
    <a class="abs social" style="left:1005px;top:2881px" aria-label="Social profile"><i></i></a>
  </footer>

</div>
</body>
</html>
```